Maple Lantern Productions web site

I need to build a website for a new company I am launching next month. Maple Lantern Productions is a company based in New England that provides sound, lighting, and audio visual services to weddings, corporate, and any other cusomer base looking for quality service for a fair price. Looking for somebody to do a full site not just the image files. I am looking to keep the colors of my logo (orange and black) and possibly grey and white. I am looking to build my site very similar to brightvaleevents.example, which is owned by a friend of mine. I like how he has the big pictures that load in to the site and the basic menu items. I'll need a gallery of photos. The designs should communicate quality, value and trust.
My website address is maplelanternco.example.
Updates

Hi and thanks to everyone for posting such great ideas for our new design.I have some items that I'd like to ask you all to focus on in your revisions.I like how http://www.brightvaleevents.example/ website has five or six high res pictures that change in a slideshow format with a caption that loads in for each one for the different types of services. Try and capture pics like these and with teh same headings as he has. The basic menu designs have been interesting.I am more fond of the menus that are more white with some orange as I dont want it to be too dark. I'm curious to see how your galleries will work and if i'll be able to edit the pages myself? I have some more info on the company for you to fill in:website address is ciderhouseco.comemail: info@ciderhouseco.comaddress: Maple Lantern Productions57 Littlefield StreetAvon, MA 02417"New England's finest DJ's, lighting and sound, video and more. Creating memories one perfect event at a time."Put this under the loading pictures as a tagline.About Cider HouseCider House Productions is a collection of New England's finest talent, ready to make your next event the one you've dreamed of. We have the skills and expertise to deliver your vision of your perfect event. From elegant weddings to themed mitzvah's, corporate av, videography and detail lighting, we offer all of the elements to make your event a success. Added Wednesday, March 1, 2017

Designer's Please also make sure that your design flows well on any device it is being viewed on as well. Thanks. Added Wednesday, March 1, 2017

Project Deadline Extended Reason: Hello designerThank you all very much for your hard work on our project. Im sorry but i need to extend the date of my project. Our parent conpany Rook Nine Prodactions sponsors Bay Youth Assemblies and we are currently at their leadership conference on the Cape. I will be back in on Monday and with your help will get this finished by Thursday the 16th. Thanks Added Thursday, March 9, 2017

Project Deadline Extended Reason: One of the designers is not responding so I now have to make revisions with other designers. I hope to get this website done over the weekends so please get your revisions as soon as possible. Thank you. I am also upgrading the budget another $75 to hopefully get some more interest on my project. Added Wednesday, March 15, 2017

Target Market(s)

Wedding - Corporate -

Industry/Entity Type

It Company

Coding

Coded - Design and coding required

Number of Pages Required

5+ page

Font styles to use
Sans Serif

Requirements
Must have
• Photo Gallery - I want to be able to edit it myself
Nice to have
• I like the look of my friends website brightvaleevents.example

```html
<!DOCTYPE html>
<html lang="en">
<head>
<meta charset="utf-8">
<title>Maple Lantern Productions</title>
<link href="https://fonts.googleapis.com/css2?family=Montserrat:wght@300;400;500;600;700&display=swap" rel="stylesheet">
<style>
  :root {
    --orange: #f2621f;
    --ink: #333333;
    --muted: #8a8a8a;
    --rule: #d9d9d9;
    --paper: #ffffff;
    --page: #eef0f2;
    --grey-btn: #c9c9c9;
  }
  * { box-sizing: border-box; margin: 0; padding: 0; }
  html, body { width: 886px; height: 1200px; overflow: hidden; background: var(--page); }
  body { font-family: "Montserrat", sans-serif; color: var(--ink); }
  .site { width: 886px; height: 1200px; background: var(--paper); position: relative; overflow: hidden; }

  /* Hero */
  .hero { position: relative; height: 370px; overflow: hidden; }
  .hero-photo {
    position: absolute; inset: 0;
    background:
      radial-gradient(ellipse 90px 40px at 300px 40px, rgba(255,246,230,.9), transparent 70%),
      radial-gradient(ellipse 70px 30px at 470px 50px, rgba(255,236,210,.85), transparent 70%),
      radial-gradient(ellipse 140px 120px at 420px 170px, rgba(250,236,244,.85), transparent 70%),
      radial-gradient(ellipse 110px 150px at 470px 190px, rgba(255,255,255,.55), transparent 70%),
      radial-gradient(ellipse 90px 130px at 360px 180px, rgba(40,34,46,.7), transparent 70%),
      radial-gradient(ellipse 230px 110px at 740px 200px, rgba(186,52,60,.75), transparent 70%),
      radial-gradient(ellipse 170px 90px at 820px 130px, rgba(120,140,190,.55), transparent 70%),
      radial-gradient(ellipse 170px 130px at 110px 180px, rgba(70,50,62,.8), transparent 70%),
      radial-gradient(ellipse 160px 60px at 120px 60px, rgba(230,228,236,.7), transparent 70%),
      linear-gradient(90deg, #5a4652 0%, #9c7d8c 32%, #c7a6b6 50%, #9a6870 68%, #6a4450 100%);
    filter: blur(2px);
  }
  .hero-fog { position: absolute; left: 0; right: 0; top: 210px; height: 160px;
    background: linear-gradient(180deg, rgba(240,228,236,0) 0%, rgba(244,234,240,.92) 40%, rgba(236,222,230,.96) 100%); }
  .hero-base { position: absolute; left: 0; right: 0; bottom: 0; height: 24px;
    background: linear-gradient(90deg, #e4d2dc, #c9a9bd 40%, #e8d6df 70%, #d8c0cc); }
  .nav {
    position: absolute; top: 18px; left: 200px; width: 528px; height: 34px;
    background: rgba(255,255,255,.22); border: 1px solid rgba(255,255,255,.35);
    display: flex; align-items: center; justify-content: space-between; padding-left: 4px;
  }
  .brand { display: flex; align-items: center; gap: 5px; font-size: 7px; font-weight: 700; color: #2a2a2a; letter-spacing: .3px; }
  .brand-dot { width: 16px; height: 16px; border-radius: 50%; background: var(--orange); }
  .menu { display: flex; height: 100%; list-style: none; font-size: 7px; color: #ffffff; }
  .menu li { display: flex; align-items: center; padding: 0 6px; }
  .menu .active { background: var(--orange); }
  .slider-dots { position: absolute; left: 159px; top: 170px; display: flex; flex-direction: column; gap: 7px; }
  .slider-dots span { width: 5px; height: 5px; border-radius: 50%; border: 1px solid #fff; }
  .slider-dots .on { background: #fff; }
  .caption {
    position: absolute; top: 256px; left: 200px; width: 486px; height: 50px;
    border-left: 1px solid #7a6a72; border-right: 1px solid #7a6a72; border-top: 1px solid #b9a8b0;
    text-align: center; font-size: 12px; line-height: 15px; color: #2e2e2e; padding-top: 12px;
  }
  .check-band { position: absolute; top: 306px; left: 0; right: 0; height: 40px; background: rgba(248,238,243,.9); }
  .check-form { position: absolute; top: 314px; left: 211px; display: flex; gap: 13px; }
  .select { width: 113px; height: 18px; background: #fff; border: 1px solid #e2dadd; font-size: 6px; color: #aaa;
    display: flex; align-items: center; justify-content: space-between; padding: 0 5px; }
  .select svg { width: 6px; height: 6px; }
  .btn-check { width: 118px; height: 18px; margin-left: 11px; background: var(--orange); color: #fff; font-size: 6px;
    display: flex; align-items: center; justify-content: center; }

  /* Intro */
  .intro { text-align: center; padding-top: 26px; height: 190px; }
  .section-title { font-size: 19px; font-weight: 400; color: #555; }
  .chevron { display: block; margin: 4px auto 0; width: 12px; height: 7px; }
  .intro p { width: 540px; margin: 18px auto 0; font-size: 6.5px; line-height: 12px; color: var(--muted); }
  .btn-help { display: inline-block; margin-top: 22px; width: 150px; height: 16px; line-height: 16px;
    background: var(--grey-btn); color: #fff; font-size: 7px; }

  /* Services */
  .services { position: relative; height: 210px; color: #fff; text-align: center; overflow: hidden; }
  .services-photo { position: absolute; inset: 0;
    background:
      radial-gradient(ellipse 70px 80px at 400px 110px, rgba(196,70,80,.55), transparent 70%),
      radial-gradient(ellipse 90px 70px at 700px 60px, rgba(160,150,170,.35), transparent 70%),
      radial-gradient(ellipse 100px 90px at 90px 80px, rgba(150,120,110,.35), transparent 70%),
      radial-gradient(ellipse at 50% 45%, #5e4046 0%, #3a2a30 45%, #201a1e 100%); }
  .services-inner { position: relative; padding-top: 20px; }
  .services .section-title { color: #fff; font-size: 17px; }
  .services .title-rule { width: 320px; height: 1px; background: rgba(255,255,255,.25); margin: 8px auto 0; }
  .service-list { display: flex; justify-content: center; gap: 40px; margin-top: 24px; }
  .service { width: 120px; }
  .service-icon { width: 26px; height: 26px; border-radius: 50%; background: #fff; margin: 0 auto;
    display: flex; align-items: center; justify-content: center; }
  .service-icon svg { width: 13px; height: 13px; }
  .service h3 { font-size: 8px; font-weight: 500; margin-top: 9px; }
  .service p { font-size: 6px; line-height: 9px; color: #ddd; margin-top: 5px; }

  /* Recent work */
  .work { text-align: center; padding-top: 24px; }
  .work .title-rule { width: 300px; height: 1px; background: var(--rule); margin: 8px auto 0; }
  .cards { display: grid; grid-template-columns: repeat(3, 200px); justify-content: center; gap: 16px; margin-top: 22px; }
  .card { border: 1px solid #e6e6e6; background: #fff; text-align: center; padding-bottom: 12px; }
  .card-photo { height: 150px; }
  .photo-corporate { background: radial-gradient(ellipse 40px 50px at 60% 30%, #e6eef8, transparent 70%), linear-gradient(180deg, #dfe6f0 0%, #8d98aa 45%, #3b3e4c 100%); }
  .photo-wedding { background: radial-gradient(ellipse 60px 40px at 70% 15%, #ffe6a0, transparent 70%), linear-gradient(160deg, #e9d38a 0%, #9bae6a 45%, #4a5a3e 100%); }
  .photo-school { background: radial-gradient(ellipse 50px 60px at 45% 45%, #f3d2b4, transparent 70%), linear-gradient(160deg, #f0c9a0 0%, #d77c6c 45%, #2e6a7e 100%); }
  .photo-lights { background: linear-gradient(180deg, #7ea0d8 0%, #4b5f9c 100%); }
  .photo-stage { background: linear-gradient(180deg, #3a1f2e 0%, #7a2a3a 60%, #c24a3a 100%); }
  .photo-party { background: linear-gradient(180deg, #2c4a6a 0%, #4a8a5a 60%, #d8b040 100%); }
  .card h4 { font-size: 10px; font-weight: 400; color: var(--orange); margin-top: 12px; }
  .card p { font-size: 6px; line-height: 9px; color: var(--muted); margin: 8px 22px 0; }
  .card-links { display: flex; justify-content: space-between; margin: 10px 18px 0; font-size: 6px; color: #555; }
  .card-links span { display: flex; align-items: center; gap: 3px; }
  .card-links svg { width: 7px; height: 7px; }
</style>
</head>
<body>
<div class="site">

  <header class="hero">
    <div class="hero-photo" role="img" aria-label="Bride and groom dancing on a fog-covered floor under stage lights, guests watching around them"></div>
    <div class="hero-fog"></div>
    <div class="hero-base"></div>

    <nav class="nav">
      <div class="brand"><span class="brand-dot"></span>MAPLE LANTERN</div>
      <ul class="menu">
        <li class="active">Home</li>
        <li>About Us</li>
        <li>Our Services</li>
        <li>Blog</li>
        <li>Contact Us</li>
      </ul>
    </nav>

    <div class="slider-dots"><span></span><span class="on"></span><span></span><span></span></div>

    <div class="caption">Use the form below to check and see if your event date is available.<br>We will contact you promptly if your date is available.</div>

    <div class="check-band"></div>
    <form class="check-form">
      <div class="select">Month<svg viewBox="0 0 6 6"><path d="M1 2l2 2 2-2" fill="none" stroke="#555" stroke-width="1"/></svg></div>
      <div class="select">Day<svg viewBox="0 0 6 6"><path d="M1 2l2 2 2-2" fill="none" stroke="#555" stroke-width="1"/></svg></div>
      <div class="select">Year<svg viewBox="0 0 6 6"><path d="M1 2l2 2 2-2" fill="none" stroke="#555" stroke-width="1"/></svg></div>
      <div class="btn-check">Check Availability</div>
    </form>
  </header>

  <section class="intro">
    <h2 class="section-title">Maple Lantern are Experts in All Type of Events</h2>
    <svg class="chevron" viewBox="0 0 12 7"><path d="M1 1l5 5 5-5" fill="none" stroke="#aaa" stroke-width="1"/></svg>
    <p>Maple Lantern Productions is a collection of New England's finest talent, ready to make your next event the one you've dreamed of. We have the skills and expertise to deliver your vision of your perfect event. From elegant weddings to themed mitzvah's, corporate av, videography and detail lighting, we offer all of the elements to make your event a success.</p>
    <span class="btn-help">How can we help you ?</span>
  </section>

  <section class="services">
    <div class="services-photo" role="img" aria-label="Guests raising glasses in a dim reception hall"></div>
    <div class="services-inner">
      <h2 class="section-title">Our Services</h2>
      <div class="title-rule"></div>
      <div class="service-list">
        <div class="service">
          <div class="service-icon"><svg viewBox="0 0 14 14"><rect x="1.5" y="4" width="11" height="8" rx="1" fill="none" stroke="#333" stroke-width="1.2"/><path d="M5 4V2.5h4V4" fill="none" stroke="#333" stroke-width="1.2"/></svg></div>
          <h3>Corporate Events</h3>
          <p>Sound, lighting and staging for meetings, launches and company nights.</p>
        </div>
        <div class="service">
          <div class="service-icon"><svg viewBox="0 0 14 14"><path d="M5 11V3l6-1.5v8" fill="none" stroke="#333" stroke-width="1.2"/><circle cx="3.8" cy="11" r="1.6" fill="#333"/><circle cx="9.8" cy="9.5" r="1.6" fill="#333"/></svg></div>
          <h3>Music Concert</h3>
          <p>Stage sound and rigs built for live bands and crowds.</p>
        </div>
        <div class="service">
          <div class="service-icon"><svg viewBox="0 0 14 14"><circle cx="5" cy="8" r="3.2" fill="none" stroke="#333" stroke-width="1.2"/><circle cx="9" cy="8" r="3.2" fill="none" stroke="#333" stroke-width="1.2"/></svg></div>
          <h3>Wedding Plane</h3>
          <p>Music, uplighting and video for your ceremony and reception night.</p>
        </div>
        <div class="service">
          <div class="service-icon"><svg viewBox="0 0 14 14"><path d="M1 5.5L7 3l6 2.5L7 8z" fill="#333"/><path d="M3.5 7v3c2 1.5 5 1.5 7 0V7" fill="none" stroke="#333" stroke-width="1.2"/></svg></div>
          <h3>School and Formal Events</h3>
          <p>DJ and lights for proms, dances and formal school events.</p>
        </div>
      </div>
    </div>
  </section>

  <section class="work">
    <h2 class="section-title">Recent Work</h2>
    <div class="title-rule"></div>
    <div class="cards">
      <article class="card">
        <div class="card-photo photo-corporate" role="img" aria-label="Audience seated before a conference stage"></div>
        <h4>Corporate Events</h4>
        <p>A full AV setup for a two day regional sales summit.</p>
        <div class="card-links">
          <span><svg viewBox="0 0 8 8"><rect x="0.5" y="1.5" width="7" height="5" fill="var(--orange)"/></svg>See Photo</span>
          <span><svg viewBox="0 0 8 8"><path d="M4 7.5C2 5 1.5 4 1.5 3a2.5 2.5 0 015 0c0 1-.5 2-2.5 4.5z" fill="var(--orange)"/></svg>See Location</span>
        </div>
      </article>
      <article class="card">
        <div class="card-photo photo-wedding" role="img" aria-label="Wedding couple with guests outdoors at golden hour"></div>
        <h4>Wedding Event</h4>
        <p>Dance floor lighting and DJ set for a barn reception.</p>
        <div class="card-links">
          <span><svg viewBox="0 0 8 8"><rect x="0.5" y="1.5" width="7" height="5" fill="var(--orange)"/></svg>See Photo</span>
          <span><svg viewBox="0 0 8 8"><path d="M4 7.5C2 5 1.5 4 1.5 3a2.5 2.5 0 015 0c0 1-.5 2-2.5 4.5z" fill="var(--orange)"/></svg>See Location</span>
        </div>
      </article>
      <article class="card">
        <div class="card-photo photo-school" role="img" aria-label="Students dancing at a high school party"></div>
        <h4>High School Party</h4>
        <p>Prom night with fog, lasers and a packed dance floor.</p>
        <div class="card-links">
          <span><svg viewBox="0 0 8 8"><rect x="0.5" y="1.5" width="7" height="5" fill="var(--orange)"/></svg>See Photo</span>
          <span><svg viewBox="0 0 8 8"><path d="M4 7.5C2 5 1.5 4 1.5 3a2.5 2.5 0 015 0c0 1-.5 2-2.5 4.5z" fill="var(--orange)"/></svg>See Location</span>
        </div>
      </article>
      <article class="card">
        <div class="card-photo photo-lights" role="img" aria-label="Event hall washed in blue uplighting"></div>
      </article>
      <article class="card">
        <div class="card-photo photo-stage" role="img" aria-label="Concert stage under red lights"></div>
      </article>
      <article class="card">
        <div class="card-photo photo-party" role="img" aria-label="Crowd at a colourful evening party"></div>
      </article>
    </div>
  </section>

</div>
</body>
</html>
```